The Marigold Venture WEBSITE DESIGN

Marigold is a not for profit working in international aid and development. The website needs to be lively not depressing,earthy rather than bling, have a dramatic impact over lightweight. It may be that a black and white with spot colour may be more impacting given the simplicity I want for the site. Marigold works in partnership with registered NGOs in Asia and Africa. At any one time it will have about five feature projects. The purpose is for people to be able to find out about the projects, the countries, the partner organisations, people's stories and then give people the opportunity to give their financial and volunteer support.

Target Market(s)

First World Donors
All ages but particularly 25 - 55

Industry/Entity Type

Human Rights

Number of Pages Required

5+ page

Font styles to use
Sans Serif

Requirements
Must have
• Simplicity
• Easy access to giving options
• Highlight stories both video and image + copy (sample in attachments)
• Lots of images over copy
Nice to have
• Interest
• Not boring
• May work in black and white with a spot colour or sepia look
Should not have
• Shiny new look
• Dont know how many pages or if it be coded or uncoded - makes no sense to me

```html
<!DOCTYPE html>
<html lang="en">
<head>
<meta charset="utf-8">
<title>The Marigold Venture</title>
<link href="https://fonts.googleapis.com/css2?family=Open+Sans:wght@400;600;700&display=swap" rel="stylesheet">
<style>
:root{
  --ink:#2b2b2b;
  --muted:#6a6a6a;
  --white:#ffffff;
  --spot:#f07d1a;
  --sky:#2c9fd8;
  --leaf:#b2c85c;
  --leaf-dark:#9bb244;
  --charcoal:#3a3a3a;
  --deep:#262626;
  --line:#d9d9d9;
}
*{margin:0;padding:0;box-sizing:border-box}
html,body{width:752px;height:1200px;overflow:hidden}
body{position:relative;font-family:"Open Sans",Arial,sans-serif;color:var(--ink);background:var(--white)}
.abs{position:absolute}

/* header */
.hero-photo{left:0;top:0;width:752px;height:326px;background:linear-gradient(180deg,#c9c9c9 0%,#8d8d8d 45%,#3d3d3d 100%)}
.brand{left:62px;top:0;width:78px;height:112px;background:var(--white);display:flex;flex-direction:column;align-items:center;justify-content:center;gap:6px;box-shadow:0 2px 6px rgba(0,0,0,.2)}
.brand-mark{width:30px;height:30px;border-radius:50%;background:var(--spot)}
.brand-name{font-size:10px;font-weight:700;color:var(--spot);text-align:center;line-height:1.2}
.call{right:24px;top:8px;font-size:9px;color:var(--white)}
.call b{color:var(--spot)}
.nav{left:252px;top:30px;width:476px;height:24px;background:var(--white);display:flex;align-items:center;justify-content:space-around;padding:0 6px}
.nav a{font-size:8px;color:var(--ink);text-decoration:none;text-transform:uppercase;padding:3px 5px}
.nav a.current{border:1px solid var(--line)}
.caption{left:0;top:276px;width:752px;height:50px;background:rgba(0,0,0,.55);color:var(--white);font-size:18px;display:flex;align-items:center;justify-content:center}
.arrow{top:170px}

/* welcome */
.welcome-title{left:62px;top:348px;font-size:21px;color:var(--ink)}
.welcome-title span{color:var(--sky)}
.welcome-title small{font-size:8px;letter-spacing:3px;color:var(--sky);text-transform:uppercase}
.welcome-lead{left:62px;top:386px;font-size:11px;font-weight:700;width:380px}
.welcome-copy{left:62px;top:406px;width:380px;font-size:8.5px;line-height:1.55;color:var(--muted)}
.welcome-copy p{margin-bottom:7px}
.btn{display:inline-flex;align-items:center;height:18px;background:var(--charcoal);color:var(--white);font-size:8px;padding-left:8px}
.btn i{display:inline-flex;align-items:center;justify-content:center;width:18px;height:18px;margin-left:8px;background:var(--spot);font-style:normal;font-weight:700;font-size:11px}
.welcome-btn{left:62px;top:488px}
.aim{left:482px;width:220px;display:flex;gap:12px}
.aim h3{font-size:11px;font-weight:700;color:var(--sky);margin-top:4px}
.aim p{font-size:7.5px;line-height:1.5;color:var(--muted);margin-top:3px}
.aim-icon{flex:none;width:36px;height:36px;border-radius:50%;display:flex;align-items:center;justify-content:center}

/* projects */
.projects{left:0;top:527px;width:752px;height:238px;background:linear-gradient(180deg,var(--leaf) 0%,var(--leaf-dark) 100%)}
.section-title{width:752px;text-align:center;font-size:21px;color:var(--ink)}
.projects .section-title{top:18px}
.projects .sub{top:50px;width:752px;text-align:center;font-size:10px;color:var(--white)}
.card{top:94px;width:200px;height:126px}
.card-photo{position:absolute;inset:0;background:linear-gradient(135deg,#8a7560,#4d4a42)}
.card-label{position:absolute;left:0;bottom:0;width:100%;height:26px;background:rgba(0,0,0,.6);color:var(--white);font-size:10px;display:flex;align-items:center;justify-content:space-between;padding-left:10px}
.card-label i{width:26px;height:26px;background:var(--spot);display:flex;align-items:center;justify-content:center;font-style:normal;font-weight:700;font-size:14px}

/* news */
.news-title{top:786px}
.news-rule{left:300px;top:820px;width:152px;height:1px;background:var(--line)}
.story{top:840px;width:300px;display:flex;gap:10px}
.story-photo{flex:none;width:82px;height:96px;background:linear-gradient(135deg,#9c8b76,#5a5046)}
.story h4{font-size:8px;font-weight:700;text-transform:uppercase}
.story p{font-size:7.5px;line-height:1.5;color:var(--muted);margin:4px 0 6px}
.story .btn{height:14px;font-size:7px}
.story .btn i{width:14px;height:14px;font-size:9px}

/* giving */
.give{left:0;top:953px;width:752px;height:188px;background:var(--deep)}
.give-left{left:0;top:0;width:752px;height:188px;background:linear-gradient(135deg,#6e6e6e,#333);clip-path:polygon(0 0,420px 0,340px 188px,0 188px)}
.give-right{left:0;top:0;width:752px;height:188px;background:linear-gradient(135deg,#555,#9a9a9a);clip-path:polygon(428px 0,752px 0,752px 188px,348px 188px)}
.give-text{top:70px;width:260px;text-align:center;color:var(--white)}
.give-text h2{font-size:20px;font-weight:400}
.give-text p{font-size:8.5px;line-height:1.5;margin-top:4px}

/* footer */
.footer{left:0;top:1141px;width:752px;height:42px;background:var(--leaf);display:flex;align-items:center;padding:0 62px}
.footer nav{display:flex;gap:18px}
.footer a{font-size:8px;color:var(--ink);text-decoration:none;text-transform:uppercase}
.social{margin-left:auto;display:flex;gap:8px}
.social span{width:18px;height:18px;border-radius:50%;background:var(--deep)}
.copyright{left:0;top:1183px;width:752px;height:17px;background:var(--deep);color:#cfcfcf;font-size:7px;display:flex;align-items:center;justify-content:center}
</style>
</head>
<body>

<div class="abs hero-photo" role="img" aria-label="Crowd of raised hands in black and white"></div>
<div class="abs brand"><span class="brand-mark"></span><span class="brand-name">The Marigold<br>Venture</span></div>
<div class="abs call">Call us: <b>555 010 4477</b></div>
<nav class="abs nav">
  <a class="current" href="#">Home</a><a href="#">About</a><a href="#">Projects</a><a href="#">Services</a><a href="#">Global Location</a><a href="#">Resources</a><a href="#">Contact Us</a>
</nav>
<svg class="abs arrow" style="left:14px" width="14" height="28" viewBox="0 0 14 28"><path d="M12 2 2 14l10 12" fill="none" stroke="#fff" stroke-width="2"/></svg>
<svg class="abs arrow" style="right:14px" width="14" height="28" viewBox="0 0 14 28"><path d="M2 2l10 12L2 26" fill="none" stroke="#fff" stroke-width="2"/></svg>
<div class="abs caption">Lorem Ipsum Dolor Sit Amet</div>

<h1 class="abs welcome-title">Welcome To <span>MARIGOLD</span> <small>Venture</small></h1>
<p class="abs welcome-lead">Lorem ipsum dolor sit amet, ex vim quem primis. Quot suavitate</p>
<div class="abs welcome-copy">
  <p>Lorem ipsum dolor sit amet, ex vim quem primis. Quot suavitate molestiae ea eos. Bellum eleifend et nec, aliquid molestiae at duo, mel vitae principes sententiae et. Ex adolescens scriptorem eam, per meis delicatissimi eu. Cu solet quaerendum sea.</p>
  <p>Lorem ipsum dolor sit amet, ex vim quem primis. Quot suavitate molestiae ea eos. Bellum eleifend et nec, aliquid molestiae at duo, mel vitae principes sententiae et.</p>
</div>
<a class="abs btn welcome-btn">Read More<i>+</i></a>

<div class="abs aim" style="top:358px">
  <span class="aim-icon" style="background:var(--sky)"><svg width="20" height="12" viewBox="0 0 20 12"><path d="M1 6c4-6 14-6 18 0-4 6-14 6-18 0z" fill="#fff"/><circle cx="10" cy="6" r="3" fill="#2c9fd8"/></svg></span>
  <div><h3>OUR VISION</h3><p>Lorem ipsum dolor sit amet, ex vim quem primis. Quot suavitate molestiae ea eos. Bellum eleifend et nec.</p></div>
</div>
<div class="abs aim" style="top:430px">
  <span class="aim-icon" style="background:#e6e6e6"><svg width="20" height="20" viewBox="0 0 20 20"><circle cx="10" cy="10" r="8" fill="none" stroke="#444" stroke-width="2"/><circle cx="10" cy="10" r="4" fill="none" stroke="#444" stroke-width="2"/><circle cx="10" cy="10" r="1.5" fill="#444"/></svg></span>
  <div><h3>OUR MISSION</h3><p>Lorem ipsum dolor sit amet, ex vim quem primis. Quot suavitate molestiae ea eos. Bellum eleifend et nec.</p></div>
</div>

<section class="abs projects">
  <h2 class="abs section-title">Current Projects</h2>
  <p class="abs sub">Lorem ipsum dolor sit amet, ex vim quem primis. Quot suavitate</p>
  <div class="abs card" style="left:62px"><div class="card-photo" role="img" aria-label="Stacks of colourful woven textiles"></div><div class="card-label">Lotus Cambodia<i>+</i></div></div>
  <div class="abs card" style="left:276px"><div class="card-photo" role="img" aria-label="Group of villagers gathered outdoors"></div><div class="card-label">Hillside Rwanda<i>+</i></div></div>
  <div class="abs card" style="left:490px"><div class="card-photo" role="img" aria-label="Children standing together at a school"></div><div class="card-label">Clearwater Kenya<i>+</i></div></div>
</section>

<h2 class="abs section-title news-title">News / Stories from Projects</h2>
<div class="abs news-rule"></div>
<article class="abs story" style="left:62px">
  <div class="story-photo" role="img" aria-label="Community members at a project site"></div>
  <div><h4>Ongoing stories and videos from overseas</h4><p>Lorem ipsum dolor sit amet, ex vim quem primis. Quot suavitate molestiae ea eos. Bellum eleifend et nec, aliquid molestiae at duo, mel vitae principes sententiae et. Ex adolescens scriptorem eam.</p><a class="btn">Read More<i>+</i></a></div>
</article>
<article class="abs story" style="left:392px">
  <div class="story-photo" role="img" aria-label="Aid workers meeting with families"></div>
  <div><h4>Articles about aid and development</h4><p>Lorem ipsum dolor sit amet, ex vim quem primis. Quot suavitate molestiae ea eos. Bellum eleifend et nec, aliquid molestiae at duo, mel vitae principes sententiae et. Ex adolescens scriptorem eam.</p><a class="btn">Read More<i>+</i></a></div>
</article>

<section class="abs give">
  <div class="abs give-left" role="img" aria-label="Black and white photo of a donor giving support"></div>
  <div class="abs give-right" role="img" aria-label="Black and white photo of volunteers working together"></div>
  <div class="abs give-text" style="left:60px"><h2>Online Giving</h2><p>Lorem ipsum dolor sit amet, ex vim quem<br>primis. Quot suavit</p></div>
  <div class="abs give-text" style="left:440px"><h2>Volunteer Vacancies</h2><p>Lorem ipsum dolor sit amet, ex vim quem<br>primis. Quot suavit</p></div>
</section>

<footer class="abs footer">
  <nav><a href="#">Home</a><a href="#">About</a><a href="#">Projects</a><a href="#">Services</a><a href="#">Global Location</a><a href="#">Resources</a><a href="#">Contact Us</a></nav>
  <div class="social"><span></span><span></span><span></span></div>
</footer>
<div class="abs copyright">Copyright 2015 : Marigold Venture : All Rights Reserved</div>

</body>
</html>
```